Hvac and insulation company needs good looking business card design

We are hvac and insulation company and looking for a new business cards that look to today standards designs

Target Market(s)

homeowners

Industry/Entity Type

Hvac

Contact Information for Business Card

Name: Walter Brinoku
Home comfort consultant
address: 4827 Dunmore St #215 Oakland, CA 94619
office: 888-316-2790
cell: 510-742-3185
Lic.# 584261
Email: walter@corvane-hvac.com
Web: corvane-hvac.com

Requirements
Must have
• clean and sleek look
Nice to have
• simple with a clean look
Should not have
• to busy business card

```html
<!DOCTYPE html>
<html lang="en">
<head>
<meta charset="utf-8">
<title>Corvane business card</title>
<link href="https://fonts.googleapis.com/css2?family=Lato:wght@400;700&display=swap" rel="stylesheet">
<style>
  :root {
    --orange: #f07f1c;
    --ink: #5b5b5b;
    --ink-soft: #6d6d6d;
    --card: #ffffff;
    --backdrop: #e6eaef;
  }
  * { margin: 0; padding: 0; box-sizing: border-box; }
  html, body { width: 1200px; height: 1000px; overflow: hidden; }
  body {
    background: var(--backdrop);
    font-family: "Lato", Arial, sans-serif;
    position: relative;
  }
  .card {
    position: absolute;
    left: 250px;
    width: 700px;
    height: 400px;
    background: var(--card);
    box-shadow: 0 8px 24px rgba(30, 50, 80, 0.18);
  }
  .card--front { top: 70px; }
  .card--back { top: 530px; }

  .brand {
    display: flex;
    align-items: center;
    gap: 14px;
    color: var(--orange);
    font-weight: 700;
    letter-spacing: 0.5px;
    line-height: 1;
  }
  .brand__mark {
    background: var(--orange);
    flex: none;
  }
  .card--front .brand {
    position: absolute;
    top: 150px;
    left: 0; right: 0;
    justify-content: center;
    font-size: 72px;
  }
  .card--front .brand__mark { width: 58px; height: 58px; }
  .front__web {
    position: absolute;
    bottom: 22px;
    left: 0; right: 0;
    text-align: center;
    font-size: 21px;
    color: var(--ink);
  }

  .card--back .brand {
    position: absolute;
    top: 46px;
    right: 30px;
    font-size: 48px;
  }
  .card--back .brand__mark { width: 40px; height: 40px; }
  .person {
    position: absolute;
    left: 36px;
    top: 112px;
    color: var(--ink-soft);
  }
  .person__name { font-size: 37px; font-weight: 400; line-height: 1.1; }
  .person__role { font-size: 21px; line-height: 1.2; }

  .rule {
    position: absolute;
    left: 33px;
    top: 193px;
    width: 667px;
    height: 2px;
    background: var(--orange);
  }
  .address-band {
    position: absolute;
    left: 210px;
    top: 193px;
    width: 490px;
    height: 34px;
  }
  .address-band svg { position: absolute; inset: 0; }
  .address-band__text {
    position: absolute;
    right: 30px;
    top: 6px;
    color: #fff;
    font-size: 18.5px;
  }

  .contacts {
    position: absolute;
    left: 36px;
    top: 246px;
    list-style: none;
    color: var(--ink-soft);
    font-size: 24px;
  }
  .contacts li {
    display: flex;
    align-items: center;
    gap: 15px;
    height: 36px;
  }
  .contacts svg { width: 20px; height: 20px; fill: var(--ink-soft); flex: none; }
  .license {
    position: absolute;
    right: 30px;
    bottom: 40px;
    font-size: 18px;
    color: var(--ink-soft);
  }
</style>
</head>
<body>

<section class="card card--front">
  <div class="brand"><span class="brand__mark"></span><span class="brand__name">corvane</span></div>
  <p class="front__web">www.corvane-hvac.com</p>
</section>

<section class="card card--back">
  <div class="brand"><span class="brand__mark"></span><span class="brand__name">corvane</span></div>

  <div class="person">
    <h1 class="person__name">Walter Brinoku</h1>
    <p class="person__role">Home comfort consultant</p>
  </div>

  <div class="rule"></div>
  <div class="address-band">
    <svg viewBox="0 0 490 34" preserveAspectRatio="none" aria-hidden="true">
      <path d="M0 0 H490 V34 H22 Q10 34 6 22 Z" fill="var(--orange)"/>
    </svg>
    <span class="address-band__text">4827 Dunmore St #215 Oakland, CA 94619</span>
  </div>

  <ul class="contacts">
    <li>
      <svg viewBox="0 0 20 20" aria-label="Office phone"><path d="M1 7c0-3 4-4 9-4s9 1 9 4v2h-4V7H5v2H1z M4 10h12l2 7H2z M10 11.5a2.5 2.5 0 1 0 0 5a2.5 2.5 0 1 0 0-5z"/></svg>
      <span>888-316-2790</span>
    </li>
    <li>
      <svg viewBox="0 0 20 20" aria-label="Cell phone"><path d="M4 1l3 0 2 5-2 2c1 2 3 4 5 5l2-2 5 2v3c0 1-1 3-3 3C9 19 1 11 1 4c0-2 2-3 3-3z"/></svg>
      <span>510-742-3185</span>
    </li>
    <li>
      <svg viewBox="0 0 20 20" aria-label="Email"><path d="M1 5h18v11H1z M2 6l8 6 8-6" fill="var(--ink-soft)" stroke="#fff" stroke-width="1.2"/></svg>
      <span>walter@corvane-hvac.com</span>
    </li>
  </ul>

  <p class="license">Lic.# 584261</p>
</section>

</body>
</html>
```